Zelvo Stationary

Design the stationary of Zelvo Promotions Group.

Zelvo is a BTL company, BTL meaning "below the line". In other words Zelvo is a Promotional Marketing company (the company that design the brands promotional activities).

The design should transmit creativity, agility, boldness.

I need:
* Bis Card
* Letter head
* Envelopes, both vertical and horizontal (for legal size), and letter envelope
* Folders
* PPT template (Title page and regular page)
* CD slip (CD envelope)
* ID card (employee card)

And what ever else you want to throw in.
Updates

Guys,

Something I missed from the brief.   The predominat color should be RED.

Also, have fun and play with the exclamation mark (!) of the logo. 

Hi guys, more comments:

Remember that Zelvo is a "creativity" agency, not in the advertising side but on the promotional side, and that should reflect on the stationary.

 I want a bold design.  Bold and yet crisp.

 

Guys, i just uploaded the Logo in AI format.

I Also uploaded the actual Zelvo Bis Card, wich I like.  So I will like to see some designs with that bis card approach.

Guys, I am so sorry, but I notice in your last post that I upladed a wrong design ("13154_promotions_group_zelvo_brief225630.ai").  The problem was that I asked the designer the file in AI format and he send me thw wrong file, and since I dont have Illustrator I could not verify it.

The differences are minor, I just already ask him the correct one (similar to the EPS file).

Sorry                                   

Just post the correct AI file : "Zelvo Logo.ai"

Reason: I'm expecting more designs to choose from and also I wont be available tomorrow to decide.

Reason: Sorry guys, but we are not there yet!

Target Market(s)

Marketing directors, Marketing Managers

Industry/Entity Type

Legal

Requirements
Must have
• Must work with the logo attached.
The predominat color should be RED.
Play and have fun with the exclamation mark (!).
Should not have
• * No old fonts

Should not be:
* boring
* Informal
* rigid

```html
<!DOCTYPE html>
<html lang="en">
<head>
<meta charset="utf-8">
<title>Zelvo Promotions Group – Stationery</title>
<link href="https://fonts.googleapis.com/css2?family=Open+Sans:wght@400;600;800&display=swap" rel="stylesheet">
<style>
  :root {
    --backdrop: #a7a9ac;
    --red: #cf2027;
    --red-dark: #8e1218;
    --red-soft: #d9574f;
    --blush: #f4d6cb;
    --grey-soft: #c9c6c6;
    --white: #ffffff;
    --ink: #231f20;
  }
  * { box-sizing: border-box; margin: 0; padding: 0; }
  html, body { width: 1200px; height: 848px; overflow: hidden; }
  body { background: var(--backdrop); font-family: "Open Sans", Arial, sans-serif; color: var(--ink); }
  .canvas { position: relative; width: 1200px; height: 848px; overflow: hidden; }
  .piece { position: absolute; }

  .wordmark { font-weight: 800; letter-spacing: -0.5px; line-height: 1; display: inline-flex; align-items: center; gap: 5px; }
  .wordmark .dot { display: inline-block; border-radius: 50%; background: currentColor; }

  .faint-name { position: absolute; font-weight: 800; line-height: 1; letter-spacing: -4px; color: var(--blush); white-space: nowrap; }

  /* Letterhead */
  .letterhead { left: 4px; top: 4px; width: 597px; height: 792px; background: var(--white); border: 3px solid var(--red); overflow: hidden; }
  .letterhead .wordmark { position: absolute; right: 38px; top: 40px; font-size: 30px; color: var(--ink); }
  .letterhead .wordmark .dot { width: 10px; height: 10px; background: var(--red); }
  .letterhead .faint-name { left: -20px; top: 590px; font-size: 150px; }
  .letterhead-footer { position: absolute; left: 0; right: 0; bottom: 0; height: 62px; background: var(--red); color: var(--red-dark); font-size: 10.5px; text-align: center; padding-top: 14px; line-height: 1.55; }

  /* Envelope */
  .envelope { left: 8px; top: 258px; width: 652px; height: 311px; background: var(--white); border-bottom: 6px solid var(--red); overflow: hidden; box-shadow: 0 0 0 1px #ddd; }
  .envelope-sender { position: absolute; left: 4px; top: 3px; font-size: 6.5px; line-height: 1.5; }
  .envelope .faint-name { left: -10px; top: 140px; font-size: 120px; }
  .envelope-lines { position: absolute; left: 422px; top: 170px; width: 187px; }
  .envelope-lines span { display: block; border-top: 1px solid var(--ink); height: 29px; }
  .envelope-lines span:first-child { width: 104px; }

  /* Business cards */
  .card-white { width: 118px; height: 196px; background: var(--white); border: 1px solid #ddd; transform: rotate(-14deg); overflow: hidden; }
  .card-white .wordmark { position: absolute; left: 8px; top: 88px; font-size: 22px; color: var(--ink); }
  .card-white .wordmark .dot { width: 7px; height: 7px; background: var(--red); }
  .card-white .details { position: absolute; left: 8px; top: 116px; font-size: 5.5px; line-height: 1.45; }
  .card-white .details .name { color: var(--red); font-size: 9px; letter-spacing: 0.5px; border-bottom: 1px solid var(--red); }
  .card-white .details .tel { font-size: 8px; }
  .card-red { width: 230px; height: 128px; background: var(--red); transform: rotate(62deg); overflow: hidden; box-shadow: -1px 1px 2px rgba(0,0,0,.2); }
  .card-red .wordmark { position: absolute; right: 12px; top: 12px; font-size: 22px; color: var(--white); }
  .card-red .wordmark .dot { width: 7px; height: 7px; }
  .card-red .details { position: absolute; left: 12px; bottom: 12px; font-size: 6px; color: var(--red-dark); line-height: 1.5; }
  .card-red .details .name { color: var(--blush); font-size: 9px; font-weight: 600; letter-spacing: .5px; }

  /* ID card */
  .id-card { left: 840px; top: 273px; width: 315px; height: 228px; background: var(--red); border: 1px solid var(--blush); overflow: hidden; }
  .id-card .band { position: absolute; left: 190px; top: 0; width: 78px; height: 100%; background: var(--red-soft); opacity: .55; }
  .id-card .band-top { position: absolute; left: 0; top: 0; width: 100%; height: 70px; background: var(--red-soft); opacity: .6; }
  .id-card .faint-name { left: 70px; top: 120px; font-size: 90px; color: var(--blush); opacity: .35; }
  .id-title { position: absolute; left: 16px; top: 15px; font-size: 18px; line-height: 1.4; letter-spacing: 1px; color: var(--blush); }
  .id-meta { position: absolute; left: 16px; top: 86px; font-size: 12px; line-height: 1.7; color: var(--white); }
  .id-photo { position: absolute; left: 193px; top: 73px; width: 72px; height: 86px; border: 1px solid var(--blush); background: linear-gradient(180deg, #e8cfc0, #f28c28); }
  .id-holder { position: absolute; left: 193px; top: 170px; font-size: 10.5px; line-height: 1.35; color: var(--white); }

  /* Folder */
  .folder { left: 610px; top: 560px; width: 349px; height: 281px; background: var(--red); }
  .folder .wordmark { position: absolute; left: 74px; top: 70px; font-size: 44px; color: var(--white); }
  .folder .wordmark .dot { width: 13px; height: 13px; }

  /* CD */
  .cd { left: 900px; top: 495px; width: 300px; height: 353px; }
</style>
</head>
<body>
<main class="canvas">

  <section class="piece letterhead" aria-label="Letterhead">
    <div class="wordmark">zelvo<span class="dot"></span></div>
    <div class="faint-name" aria-hidden="true">zelvo</div>
    <footer class="letterhead-footer">
      27 Calle Mira, Los Prados, Santo Domingo, Dominican Republic<br>
      Phone: +809 555.0142 / Fax: +809 555.0143 / www.zelvo.com.do
    </footer>
  </section>

  <section class="piece envelope" aria-label="Envelope">
    <p class="envelope-sender">27 Calle Mira, Los Prados, Santo Domingo, Dominican Republic<br>Phone: +809 555.0142 / Fax: +809 555.0143 / www.zelvo.com.do</p>
    <div class="faint-name" aria-hidden="true">zelvo</div>
    <div class="envelope-lines"><span></span><span></span><span></span><span></span></div>
  </section>

  <section class="piece card-white" style="left:700px;top:12px;" aria-hidden="true"></section>
  <section class="piece card-white" style="left:660px;top:28px;" aria-hidden="true"></section>
  <section class="piece card-white" style="left:625px;top:58px;" aria-label="Business card">
    <div class="wordmark">zelvo<span class="dot"></span></div>
    <div class="details">
      <div class="name">MARCO DELANE</div>
      <div class="tel">809-555-0171</div>
      marco.delane@zelvo.com.do<br>27 Calle Mira, Los Prados<br>Phone: +809 555.0142<br>Fax: +809 555.0143<br>www.zelvo.com.do
    </div>
  </section>

  <section class="piece card-red" style="left:935px;top:70px;" aria-hidden="true"></section>
  <section class="piece card-red" style="left:905px;top:82px;" aria-label="Business card">
    <div class="wordmark">zelvo<span class="dot"></span></div>
    <div class="details">
      <div class="name">PABLO SERRAT</div>
      809-555-0188<br>pablo.serrat@zelvo.com.do<br>27 Calle Mira, Los Prados<br>Phone: +809 555.0142
    </div>
  </section>

  <section class="piece cd" aria-label="CD slip">
    <svg width="300" height="353" viewBox="0 0 300 353">
      <defs><clipPath id="disc"><circle cx="135" cy="190" r="180"/></clipPath></defs>
      <circle cx="135" cy="190" r="180" fill="var(--white)" stroke="#d0d0d0"/>
      <g clip-path="url(#disc)">
        <rect x="-40" y="230" width="420" height="48" fill="var(--red)" transform="rotate(35 135 190)"/>
        <text x="60" y="258" fill="var(--white)" font-size="17" font-family="Open Sans, sans-serif" transform="rotate(35 135 190)">tecum vievere possum</text>
      </g>
      <circle cx="120" cy="185" r="55" fill="none" stroke="#d0d0d0"/>
      <circle cx="120" cy="185" r="20" fill="none" stroke="#d0d0d0"/>
    </svg>
  </section>

  <section class="piece folder" aria-label="Folder">
    <div class="wordmark">zelvo<span class="dot"></span></div>
  </section>

  <section class="piece id-card" aria-label="Employee identity card">
    <div class="band-top"></div>
    <div class="band"></div>
    <div class="faint-name" aria-hidden="true">zelvo</div>
    <h2 class="id-title">IDENTITY<br>CARD</h2>
    <p class="id-meta">No. 20417-5521<br>Valid to 12/12</p>
    <div class="id-photo" role="img" aria-label="Employee portrait"></div>
    <p class="id-holder">MARCO DELANE<br>manager</p>
  </section>

</main>
</body>
</html>
```